Amber Hollow Gin bottle label

We are looking for a label design for our new gin 'Amber Hollow Gin' The gin will be transparent and be in a 50cl bottle at 40%abv. The type of bottle we are using is on the attachment. We would like the label to be shabby chic style in design, suitable as a wedding gift, for couples, valentines, anniversarys.
'CAN YOU PLEASE SEE THE ATTACHMENT AS TO STYLE OF DESIGN'
Thank you

```html
<!DOCTYPE html>
<html lang="en">
<head>
<meta charset="utf-8">
<title>Amber Hollow Gin – Bottle Label</title>
<link rel="stylesheet" href="https://fonts.googleapis.com/css2?family=Great+Vibes&family=Sansita:wght@700&family=Arimo&display=swap">
<style>
  :root {
    --backdrop: #aab3c1;
    --paper: #f5eed6;
    --paper-light: #fdfbf1;
    --frame-brown: #4b2616;
    --frame-edge: #8a5a3c;
    --heart-light: #f6c9d3;
    --heart-deep: #dc9aae;
    --ink-brown: #4a2717;
    --ink-soft: #3d3d3d;
    --ornament: #c99aa0;
    --bloom: #efb3a0;
    --bloom-light: #f6d3c6;
    --leaf: #a9cbbf;
  }
  * { margin: 0; padding: 0; box-sizing: border-box; }
  html, body { width: 794px; height: 1200px; overflow: hidden; background: var(--backdrop); }
  .canvas { position: relative; width: 794px; height: 1200px; overflow: hidden; background: var(--backdrop); }
  .label { position: absolute; left: 47px; top: 144px; width: 700px; height: 912px; }
  .label-art { position: absolute; inset: 0; width: 700px; height: 912px; }
  .brand-name {
    position: absolute; left: 0; right: 0; top: 192px; text-align: center;
    font-family: "Great Vibes", cursive; font-weight: 400; font-size: 90px; line-height: 1;
    color: var(--ink-brown); white-space: nowrap;
  }
  .divider-ornament {
    position: absolute; left: 285px; top: 300px; width: 130px; height: 105px;
    border-radius: 12px;
    background: var(--ornament);
  }
  .spirit-type {
    position: absolute; left: 0; right: 0; top: 440px; text-align: center;
    font-family: "Sansita", sans-serif; font-weight: 700; font-size: 90px; line-height: 1;
    color: var(--ink-brown); letter-spacing: -1px;
  }
  .floral-spray {
    position: absolute; left: 60px; top: 570px; width: 580px; height: 250px;
    border-radius: 24px;
    background: linear-gradient(90deg, var(--leaf) 0%, var(--bloom-light) 22%, var(--bloom) 50%, var(--bloom-light) 78%, var(--leaf) 100%);
  }
  .abv {
    position: absolute; left: 0; right: 0; top: 848px; text-align: center;
    font-family: "Arimo", sans-serif; font-size: 22px; line-height: 1; color: var(--ink-soft);
  }
</style>
</head>
<body>
<main class="canvas">
  <section class="label">
    <svg class="label-art" viewBox="0 0 700 912" aria-hidden="true">
      <defs>
        <radialGradient id="paperGlow" cx="50%" cy="55%" r="65%">
          <stop offset="0%" stop-color="var(--paper-light)"/>
          <stop offset="100%" stop-color="var(--paper)"/>
        </radialGradient>
        <linearGradient id="heartFill" x1="0" y1="0" x2="0" y2="1">
          <stop offset="0%" stop-color="var(--heart-deep)"/>
          <stop offset="45%" stop-color="var(--heart-light)"/>
          <stop offset="100%" stop-color="var(--heart-deep)"/>
        </linearGradient>
      </defs>
      <path class="torn-frame" fill="url(#paperGlow)" stroke="var(--frame-brown)" stroke-width="7" stroke-linejoin="round"
        d="M6 8 L60 12 L95 6 L150 10 L210 5 L270 11 L330 6 L400 12 L455 7 L520 11 L580 5 L640 10 L694 6
           L690 70 L696 120 L689 180 L695 250 L688 320 L694 380 L686 420 L693 470 L688 540 L695 600 L689 660 L694 720 L688 790 L695 850 L692 906
           L630 902 L575 907 L510 901 L450 906 L390 900 L330 906 L270 901 L210 907 L150 902 L90 906 L30 901 L8 905
           L12 840 L5 780 L11 720 L6 660 L13 610 L7 560 L12 500 L4 450 L10 390 L6 330 L13 280 L7 220 L11 160 L5 100 L10 50 Z"/>
      <path class="heart" fill="url(#heartFill)"
        d="M350 150 C305 45 55 55 50 215 C45 350 255 430 350 540 C445 430 655 350 650 215 C645 55 395 45 350 150 Z"/>
    </svg>
    <h1 class="brand-name">Amber Hollow</h1>
    <div class="divider-ornament" role="img" aria-label="Scrolled flourish divider with a small filigree heart"></div>
    <p class="spirit-type">GIN</p>
    <div class="floral-spray" role="img" aria-label="Watercolour spray of peach peonies with eucalyptus leaves and falling petals"></div>
    <p class="abv">40%abv</p>
  </section>
</main>
</body>
</html>
```